Funky web design for eCommerce product site

This is the theme we want to use: http://marketstall.themevault-demo.test/home/home-product-landing-2/

The design must fit cleanly into the theme to minimise custom coding.

We are rebranding a health supplement product. 1 product, but comes in different quantities/packs.

The previous websites have been clunky, ugly, with poor design and very little purpose. We need a clean UI that takes the user through how it works, to the products, to the cart, all with a simple to use platform.

Tone of voice & Key Messages:

Funny, witty, relates to 28-40 audience. Product is for people who don't want to ruin their next day at work with a hangover OR cherish their weekends so much they would never want to waste a Saturday or Sunday. The characters telling the brand stories are two scientists

Full brief is attached with links to branding elements.

Target Market(s)

Men and women who love to drink alcohol and want to prevent hangovers.

Identified audience is 30-55 years (we will start by targeting 28-40), the USP is superior product performance based on health benefits of reduction of alcohol through the liver, secondarily hangover symptom reduction. Premium brand for health conscious consumers. Superior replacement for the go-to-hangover meds, ie. Feveril, Dolacin, Vitaroso - aids the process and digestion as opposed to inhibiting. Brand look and feel re-design to be relevant to identified target audience.

Industry/Entity Type

Health Product

Font styles to use
Other font styles liked:
• Norwester/Lato or Bangers/Oxygen

Colors

Designer to choose colors to be used in the design.

Requirements
Must have
• This site covers a lot of what we want: https://www.sitegrove-example.com.au/ecommerce-website-features/
• MOBILE FIRST DESIGN
• Video on homepage
• Email popup
• Add to cart from home page
• Coupon code
• Chatterbox Relay Chat
• Quick fill credit card info at checkout
• Reviews
• Mobile friendly
• Detailed shipping info (can be a secondary header bar with FREE shipping over $30 promo)
• Money back guarantee page (return policy)
• Contact page phone, email, and an online form + connect with us on Friendspace and Snapgrid
• Favicon
• Referral program
• SEO text boxes on home page
• Newsletter sign up in footer
• Sections to show: REVIEWS/TESTIMONIALS and REFER A FRIEND and MONEY BACK GUARANTEE
• Needs a call to action SHOP NOW button at the bottom of the page (see https://plumvo.example/)
• Needs payment icons in the footer (quidpass / Norda / Cardium for now)
• Colours and fonts should match branding guidelines.
Nice to have
• Loves design wise: https://postwren.example/
• Other inspiration
• https://www.boardlyn.example/pin/474285404494163209/
• https://www.boardlyn.example/pin/475200198166081933/
• https://www.boardlyn.example/pin/181692166197049862/
• https://www.boardlyn.example/pin/293156256984803604/
• https://www.boardlyn.example/pin/482025966346092082/
• https://www.boardlyn.example/pin/425238389801779277/
• http://fervent.kellotrap.example/
• https://brisklodge.example/
Should not have
• These are examples of the old site:
• http://www.hepranusa.example/
• http://demo.quarrywebworks.example/hepran-cms/
• We are moving away from the green
• These are examples of sites we do NOT want to see.

```html
<!DOCTYPE html>
<html lang="en">
<head>
<meta charset="utf-8">
<title>Hepran – Home</title>
<link rel="stylesheet" href="https://fonts.googleapis.com/css2?family=Oswald:wght@400;500;600&family=Lato:wght@300;400;700&display=swap">
<style>
:root{
  --ink:#2a2a2a;
  --body:#6d6d6d;
  --teal:#2aa9b3;
  --teal-deep:#1d8f99;
  --cyan:#43c8d8;
  --purple:#8a4fa3;
  --lavender:#c98be0;
  --paper:#ffffff;
  --mist:#f1f1f1;
  --night:#1f1f1f;
  --night-2:#151515;
  --green:#2fb24a;
}
*{box-sizing:border-box;margin:0;padding:0}
html,body{width:1200px;height:4225px;overflow:hidden}
body{position:relative;font-family:"Lato",sans-serif;color:var(--body);background:var(--paper)}
.abs{position:absolute}
.display{font-family:"Oswald",sans-serif;font-weight:500;letter-spacing:1px;text-transform:uppercase}
p.copy{font-size:15px;line-height:26px}
.btn{position:absolute;display:flex;align-items:center;justify-content:center;font-family:"Oswald",sans-serif;font-size:15px;letter-spacing:1px;color:#fff;text-transform:uppercase}
.btn-purple{background:var(--purple)}
.btn-teal{background:var(--teal)}

/* header hero */
.hero{left:0;top:0;width:1200px;height:654px;background:radial-gradient(ellipse at 70% 60%,#4a3a2c 0%,#2a2420 45%,#121212 100%)}
.brand{left:85px;top:22px;font-family:"Lato",sans-serif;font-weight:300;font-size:54px;letter-spacing:4px;color:#fff}
.nav{left:479px;top:44px;display:flex;gap:34px;font-family:"Oswald",sans-serif;font-size:13px;letter-spacing:1px;color:#fff}
.nav-icons{left:1062px;top:42px;display:flex;gap:20px}

/* promo */
.promo{left:0;top:654px;width:1200px;height:95px;background:var(--teal)}
.promo-title{left:169px;top:676px;font-size:38px;color:#fff}
.coupon{left:789px;top:676px;width:332px;height:51px;border:2px solid #fff;color:#fff;font-family:"Oswald",sans-serif;font-size:18px;letter-spacing:1px;display:flex;align-items:center;justify-content:center}

.band{left:0;width:1200px}
.shot{position:absolute}
h2.head{position:absolute;font-family:"Oswald",sans-serif;font-weight:500;font-size:34px;letter-spacing:1px;color:var(--ink);text-transform:uppercase}

/* what is */
.what-band{top:1211px;height:324px;background:linear-gradient(120deg,#2b2b2b,#4b4236 55%,#222)}
h2.what-title{left:0;width:1200px;text-align:center;color:#fff;font-size:44px;top:1268px}
.what-copy{left:270px;top:1340px;width:660px;text-align:center;color:#eee}

/* reviews */
.reviews-band{top:2879px;height:417px;background:linear-gradient(135deg,#1f8f9b,#2fb3bf 40%,#1d8691 70%,#36bcc7)}
h2.reviews-title{left:0;width:1200px;text-align:center;color:#fff;top:2914px}
.avatar{left:544px;top:2986px;width:112px;height:112px;border-radius:50%;background:linear-gradient(#c99a7d,#6b4a3a);border:4px solid #fff}
.quote{left:240px;top:3118px;width:720px;text-align:center;color:#fff;font-style:italic}
.reviewer{left:0;width:1200px;top:3204px;text-align:center;color:#fff;font-family:"Oswald",sans-serif;font-size:15px;letter-spacing:1px}

/* product card */
.shop-band{top:3296px;height:479px;background:var(--paper)}
.card{left:85px;top:3358px;width:1028px;height:360px;background:linear-gradient(#f4f4f4,#dcdcdc)}
.price{left:141px;top:3492px;font-family:"Oswald",sans-serif;font-size:30px;color:var(--purple)}

/* footer */
.footer{top:3775px;height:450px;background:var(--night)}
.foot-head{font-family:"Oswald",sans-serif;font-size:20px;letter-spacing:1px;color:#fff;text-transform:uppercase}
.foot-copy{font-size:13px;line-height:21px;color:#aaa}
.field{background:#fff;color:#999;font-size:13px;display:flex;align-items:center;padding-left:12px}
.legal{left:0;width:1200px;top:4066px;display:flex;justify-content:center;gap:34px;font-family:"Oswald",sans-serif;font-size:12px;letter-spacing:1px;color:#ccc}
.pay-row{left:0;width:1200px;top:4118px;display:flex;justify-content:center;align-items:center;gap:12px}
.social{width:34px;height:34px;border:1px solid #fff;border-radius:50%}
.pay{height:26px;padding:0 8px;background:#fff;color:#333;font-size:11px;font-weight:700;display:flex;align-items:center}
.copyright{left:0;width:1200px;top:4180px;text-align:center;font-size:12px;color:#888}
.chat{left:859px;top:4169px;width:268px;height:56px;background:var(--teal);color:#fff;font-family:"Oswald",sans-serif;font-size:14px;letter-spacing:1px;display:flex;align-items:center;gap:12px;padding-left:20px}
.chat-dot{width:14px;height:14px;border-radius:50%;background:#fff}

/* popup */
.scrim{left:0;top:0;width:1200px;height:4225px;background:rgba(0,0,0,.72)}
.popup{left:304px;top:118px;width:592px;height:389px;background:linear-gradient(135deg,#5fd6e4,#3ec3d4 45%,#72dbe8 70%,#35bcce)}
.popup-brand{left:0;width:592px;top:46px;text-align:center;font-weight:300;font-size:44px;letter-spacing:4px;color:#fff}
.popup .field{position:absolute;left:85px;width:422px;height:48px}
.popup-submit{left:237px;top:276px;width:124px;height:43px;background:var(--lavender)}
.close{left:866px;top:116px;width:60px;height:60px;border-radius:50%;background:#1a1a1a;border:3px solid #fff;display:flex;align-items:center;justify-content:center}
</style>
</head>
<body>

<!-- header -->
<section class="abs hero" role="img" aria-label="Photo of friends toasting at a dimly lit bar"></section>
<div class="abs brand">HEPRAN</div>
<nav class="abs nav">
  <span>HOME</span><span>SHOP</span><span>THE SCIENCE</span><span>REVIEWS &amp; FAQS</span><span>GET FREE HEPRAN</span><span>BLOG</span>
</nav>
<div class="abs nav-icons">
  <svg width="20" height="20" viewBox="0 0 20 20" fill="none" stroke="#fff" stroke-width="1.6"><path d="M1 3h3l2.5 10h10l2-7H5"/><circle cx="8" cy="17" r="1.3"/><circle cx="15" cy="17" r="1.3"/></svg>
  <svg width="20" height="20" viewBox="0 0 20 20" fill="none" stroke="#fff" stroke-width="1.8"><circle cx="8" cy="8" r="6"/><path d="M12.5 12.5L18 18"/></svg>
</div>

<!-- promo bar -->
<section class="abs promo"></section>
<div class="abs display promo-title">FREE SHIPPING OVER $30 PROMO</div>
<div class="abs coupon">COUPON CODE: SITE30</div>

<!-- our products -->
<section class="abs band" style="top:749px;height:462px;background:var(--mist)"></section>
<h2 class="head" style="left:85px;top:808px">OUR PRODUCTS</h2>
<p class="abs copy" style="left:85px;top:870px;width:500px">HEPRAN is a German patented formula, a drink with a unique blend of natural mineral salts and trace elements that supports the body's natural ability to process alcohol and to reduce the toll of a night out.</p>
<p class="abs copy" style="left:85px;top:1000px;width:500px">A refreshing fast-acting powdered supplement. A single sachet is a 15 g serve, lightly flavoured with citrus and only 20 calories.</p>
<div class="btn btn-purple" style="left:85px;top:1113px;width:123px;height:42px">READ MORE</div>
<div class="shot" role="img" aria-label="Product display box of sachets" style="left:648px;top:804px;width:479px;height:379px;background:linear-gradient(135deg,#f5f5f5 0%,#e4e4e4 40%,#4cbf5c 60%,#2a9c3e 100%)"></div>

<!-- what is -->
<section class="abs band what-band" role="img" aria-label="Photo of a bartender pouring a beer"></section>
<h2 class="head what-title">WHAT IS HEPRAN</h2>
<p class="abs copy what-copy">HEPRAN is a German patented formula, a drink with a unique blend of natural mineral salts and trace elements that helps the body process alcohol and recover faster.</p>

<!-- how does it work -->
<section class="abs band" style="top:1535px;height:479px;background:var(--paper)"></section>
<h2 class="head" style="left:118px;top:1638px">HOW DOES HEPRAN WORK</h2>
<p class="abs copy" style="left:118px;top:1700px;width:500px">HEPRAN is a German patented formula, a drink with a unique blend of natural mineral salts and trace elements that supports the liver's own process, helping reduce the effects of a big night and keeping your next morning on track.</p>
<div class="btn btn-purple" style="left:118px;top:1896px;width:124px;height:42px">READ MORE</div>
<div class="shot" role="img" aria-label="Stack of product sachets" style="left:634px;top:1606px;width:507px;height:366px;background:linear-gradient(135deg,#eaeaea 0%,#3fb653 45%,#2a9c3e 100%)"></div>

<!-- when -->
<section class="abs band" style="top:2014px;height:465px;background:var(--paper)"></section>
<div class="shot" role="img" aria-label="Stack of product sachets" style="left:113px;top:2085px;width:450px;height:338px;background:linear-gradient(135deg,#3fb653 0%,#2a9c3e 45%,#eaeaea 100%)"></div>
<h2 class="head" style="left:617px;top:2063px">WHEN DO I TAKE HEPRAN</h2>
<p class="abs copy" style="left:617px;top:2125px;width:500px">Take one sachet before your first drink and another before bed. The blend of mineral salts and trace elements gets to work while you sleep, so you wake up ready for the day.</p>
<div class="btn btn-purple" style="left:617px;top:2324px;width:124px;height:42px">READ MORE</div>

<!-- how do I take -->
<section class="abs band" style="top:2479px;height:400px;background:var(--paper)"></section>
<h2 class="head" style="left:118px;top:2511px">HOW DO I TAKE HEPRAN</h2>
<p class="abs copy" style="left:118px;top:2573px;width:500px">Stir one 15 g sachet into a glass of cold water and drink it straight away. It is light, fizzy and only 20 calories, with no sugar added and nothing artificial.</p>
<div class="btn btn-purple" style="left:118px;top:2775px;width:124px;height:42px">READ MORE</div>
<div class="shot" role="img" aria-label="Stack of product sachets" style="left:648px;top:2507px;width:507px;height:254px;background:linear-gradient(135deg,#eaeaea 0%,#3fb653 45%,#2a9c3e 100%)"></div>

<!-- reviews -->
<section class="abs band reviews-band"></section>
<h2 class="head reviews-title">REVIEWS/TESTIMONIALS</h2>
<div class="abs avatar" role="img" aria-label="Customer portrait"></div>
<p class="abs copy quote">"I was sceptical at first, but after my sister's wedding I woke up fresh and went for a run. Now I never head out without a sachet in my bag. Saturdays are mine again."</p>
<div class="abs reviewer">MARLA QUINT<br><span style="font-family:Lato,sans-serif;font-size:12px;opacity:.8">SYDNEY</span></div>

<!-- product card -->
<section class="abs band shop-band"></section>
<div class="abs card"></div>
<div class="shot" role="img" aria-label="Product display box of sachets" style="left:648px;top:3366px;width:479px;height:296px;background:linear-gradient(135deg,#f0f0f0 0%,#45b957 50%,#2a9c3e 100%)"></div>
<h2 class="head" style="left:141px;top:3435px;font-size:32px">HEPRAN 25 X 15G SACHET</h2>
<div class="abs price">$137.50</div>
<p class="abs copy" style="left:141px;top:3548px;width:420px;font-size:13px;line-height:22px">Stock up on twenty-five single serves for weddings, birthdays and every long weekend in between.</p>
<div class="btn btn-teal" style="left:146px;top:3610px;width:147px;height:43px">SHOP</div>

<!-- footer -->
<section class="abs band footer"></section>
<div class="abs foot-head" style="left:85px;top:3826px">REFERRAL PROGRAM</div>
<p class="abs foot-copy" style="left:85px;top:3866px;width:500px">Refer a friend and you both get a free pack of sachets on your next order. Share your code, pass on the good mornings and save together.</p>
<div class="btn btn-teal" style="left:85px;top:3958px;width:112px;height:42px;font-size:13px">REFER</div>
<div class="abs foot-head" style="left:654px;top:3826px">NEWSLETTER</div>
<p class="abs foot-copy" style="left:654px;top:3860px;width:460px">Get tips, offers and news first.</p>
<div class="abs field" style="left:654px;top:3902px;width:459px;height:36px">Enter Your Email</div>
<div class="btn btn-teal" style="left:654px;top:3958px;width:112px;height:42px;font-size:13px">SUBMIT</div>
<div class="abs legal"><span>PRIVACY</span><span>|</span><span>TERMS &amp; CONDITIONS</span><span>|</span><span>ABOUT</span><span>|</span><span>MONEY BACK GUARANTEE</span></div>
<div class="abs pay-row">
  <div class="social" aria-label="Friendspace"></div>
  <div class="social" aria-label="Linkory"></div>
  <div class="pay">Norda</div>
  <div class="pay">Cardium</div>
  <div class="pay">Quidpass</div>
</div>
<div class="abs copyright">© Copyright 2017 Hepran All Rights Reserved</div>
<div class="abs chat"><span class="chat-dot"></span>CHATTERBOX RELAY CHAT</div>

<!-- email popup -->
<div class="abs scrim"></div>
<div class="abs popup" role="dialog" aria-label="Email sign up">
  <div class="abs popup-brand">HEPRAN</div>
  <div class="field" style="top:138px">Enter Your Email</div>
  <div class="field" style="top:198px">Password</div>
  <div class="btn popup-submit">SUBMIT</div>
</div>
<div class="abs close">
  <svg width="18" height="18" viewBox="0 0 18 18" stroke="#fff" stroke-width="3"><path d="M3 3l12 12M15 3L3 15"/></svg>
</div>

</body>
</html>
```